KRV Business Card

Looking for a business card for my restaurant group I own. Four different concepts:

Copperfield Alehouse
Bristow Alehouse
Tanager's Stone Hearth Kitchen
Pellston Patty Company

Card doesn't need to include all the logos.

```html
<!DOCTYPE html>
<html lang="en">
<head>
<meta charset="UTF-8">
<title>KRV Business Card</title>
<link href="https://fonts.googleapis.com/css2?family=Poppins:wght@400;500;600&display=swap" rel="stylesheet">
<style>
  :root {
    --backdrop: #231f20;
    --paper: #ffffff;
    --gold: #d2af6b;
    --ink: #4a4a4a;
    --slate: #6d6e71;
  }
  * { margin: 0; padding: 0; box-sizing: border-box; }
  html, body { width: 1125px; height: 1200px; overflow: hidden; }
  body {
    background: var(--backdrop);
    font-family: "Poppins", sans-serif;
    position: relative;
  }
  .card {
    position: absolute;
    left: 171px;
    width: 826px;
    height: 472px;
  }
  .card--front { top: 106px; background: var(--paper); }
  .card--back { top: 639px; background: var(--gold); }

  .brand {
    position: absolute;
    left: 49px;
    top: 150px;
    color: var(--gold);
    font-weight: 600;
    font-size: 36px;
    line-height: 42px;
    letter-spacing: 3px;
    text-transform: uppercase;
  }
  .address {
    position: absolute;
    left: 49px;
    top: 247px;
    color: var(--ink);
    font-size: 20px;
    line-height: 26px;
  }
  .contacts {
    position: absolute;
    left: 49px;
    top: 307px;
    list-style: none;
    color: var(--ink);
    font-size: 20px;
    line-height: 26.5px;
  }
  .contacts li { display: flex; align-items: center; }
  .contacts svg { width: 19px; height: 19px; margin-right: 13px; fill: var(--gold); flex: none; }

  .person {
    position: absolute;
    right: 37px;
    top: 328px;
    text-align: right;
  }
  .person__name { color: var(--gold); font-weight: 600; font-size: 31px; line-height: 36px; }
  .person__title { color: var(--slate); font-weight: 500; font-size: 21px; line-height: 26px; }

  .monogram {
    position: absolute;
    left: 0; right: 0;
    top: 108px;
    text-align: center;
    color: var(--paper);
    font-weight: 600;
    font-size: 180px;
    line-height: 200px;
    letter-spacing: 8px;
  }
  .back-url {
    position: absolute;
    left: 0; right: 0;
    top: 392px;
    text-align: center;
    color: var(--paper);
    font-size: 19px;
    letter-spacing: 4.6px;
  }
</style>
</head>
<body>
  <section class="card card--front">
    <div class="brand">Kestrel Ridge<br>Ventures</div>
    <p class="address">4210 Larkspur Way<br>Juneau, Alaska 99801</p>
    <ul class="contacts">
      <li><svg viewBox="0 0 24 24"><path d="M6.6 10.8a15 15 0 0 0 6.6 6.6l2.2-2.2c.3-.3.7-.4 1-.2 1.1.4 2.3.6 3.6.6.6 0 1 .4 1 1V20c0 .6-.4 1-1 1A17 17 0 0 1 3 4c0-.6.4-1 1-1h3.5c.6 0 1 .4 1 1 0 1.3.2 2.5.6 3.6.1.3 0 .7-.2 1z"/></svg>907-214-6630</li>
      <li><svg viewBox="0 0 24 24"><path d="M7 1h10a2 2 0 0 1 2 2v18a2 2 0 0 1-2 2H7a2 2 0 0 1-2-2V3a2 2 0 0 1 2-2zm0 3v14h10V4zm5 15.5a1 1 0 1 0 0 2 1 1 0 0 0 0-2z"/></svg>907-518-2274</li>
      <li><svg viewBox="0 0 24 24"><path d="M7 2h10v5H7zM4 8h16a2 2 0 0 1 2 2v7h-4v5H6v-5H2v-7a2 2 0 0 1 2-2zm4 8v4h8v-4z"/></svg>907-326-4819</li>
      <li><svg viewBox="0 0 24 24"><path d="M2 5h20v14H2zm2 2v.5l8 5.5 8-5.5V7zm0 2.9V17h16V9.9l-8 5.5z"/></svg>name@kestrelridgeventures.com</li>
      <li><svg viewBox="0 0 24 24"><path d="M12 2a10 10 0 1 0 0 20 10 10 0 0 0 0-20zm-1 17.9A8 8 0 0 1 4.2 10L9 14.9V16a2 2 0 0 0 2 2zm6.9-2.5A2 2 0 0 0 16 16h-1v-3a1 1 0 0 0-1-1H8v-2h2a1 1 0 0 0 1-1V7h2a2 2 0 0 0 2-2v-.4a8 8 0 0 1 2.9 12.8z"/></svg>www.kestrelridgeventures.com</li>
    </ul>
    <div class="person">
      <p class="person__name">Daniel Hart</p>
      <p class="person__title">President</p>
    </div>
  </section>

  <section class="card card--back">
    <div class="monogram">KRV</div>
    <p class="back-url">WWW.KESTRELRIDGEVENTURES.COM</p>
  </section>
</body>
</html>
```